Keystone Trench Co Business Card*

Looking for a professional, clean and crisp business card

I am in the underground utilities industry and am just looking for a really impressive business card. I would like our card to be white with our symbol crisp and clear with it protruding. I also have a business partner that will require his name and info on the card once the design is set. I would like to have our website info on the card which is;
http://keystonetrenchco.example/

Contact Information for Business Card

Website, contact name, number and email

```html
<!DOCTYPE html>
<html lang="en">
<head>
<meta charset="utf-8">
<title>Keystone Trench Co — Business Card</title>
<link rel="stylesheet" href="https://fonts.googleapis.com/css2?family=Montserrat:wght@700&family=Open+Sans:wght@400;600;700&display=swap">
<style>
  :root {
    --stage: #e9eaee;
    --card-dark: #1b1b1d;
    --card-light: #ffffff;
    --brand-blue: #3a5ca8;
    --ink: #1e1e1e;
    --accent-red: #e0242b;
    --silver: #c9cacd;
    --rule: #3c3c3c;
  }
  * { box-sizing: border-box; margin: 0; padding: 0; }
  html, body { width: 1200px; height: 800px; overflow: hidden; }
  body {
    background: var(--stage);
    font-family: "Open Sans", Arial, sans-serif;
    color: var(--ink);
    position: relative;
  }
  .card {
    position: absolute;
    left: 320px;
    width: 560px;
    height: 320px;
    overflow: hidden;
    box-shadow: 0 6px 18px rgba(0,0,0,0.18);
  }
  .card::after {
    content: "";
    position: absolute;
    left: 0; right: 0; bottom: 0;
    height: 8px;
    background: var(--brand-blue);
  }
  .card--back { top: 50px; background: var(--card-dark); }
  .card--front { top: 420px; background: var(--card-light); }

  .wordmark {
    display: flex;
    align-items: center;
    gap: 10px;
    font-family: "Open Sans", Arial, sans-serif;
    font-weight: 700;
    white-space: nowrap;
  }
  .wordmark__dot { border-radius: 50%; flex: none; }

  .card--back .wordmark {
    position: absolute;
    left: 50%; top: 118px;
    transform: translateX(-50%);
    font-size: 30px;
    color: var(--silver);
  }
  .card--back .wordmark__dot { width: 22px; height: 22px; background: var(--silver); }
  .back-url {
    position: absolute;
    right: 34px; bottom: 30px;
    font-size: 15px;
    letter-spacing: 0.5px;
    color: #f2f2f2;
  }

  .card--front .wordmark {
    position: absolute;
    left: 30px; top: 60px;
    font-size: 20px;
    color: var(--ink);
  }
  .card--front .wordmark__dot { width: 18px; height: 18px; background: var(--ink); }
  .front-tab {
    position: absolute;
    right: 30px; top: 0;
    width: 12px; height: 34px;
    background: var(--brand-blue);
  }
  .person {
    position: absolute;
    right: 52px; top: 40px;
    text-align: right;
  }
  .person__name {
    font-family: "Montserrat", Arial, sans-serif;
    font-weight: 700;
    font-size: 26px;
    letter-spacing: 0.5px;
    color: var(--brand-blue);
  }
  .person__role { font-size: 15px; letter-spacing: 0.5px; margin-top: -2px; }
  .divider {
    position: absolute;
    left: 34px; right: 34px; top: 142px;
    height: 1px;
    background: var(--rule);
  }
  .contact-list {
    position: absolute;
    left: 34px; top: 180px;
    list-style: none;
    font-size: 15px;
    line-height: 27px;
  }
  .contact-list li { display: flex; align-items: center; gap: 10px; }
  .icon { width: 15px; height: 15px; flex: none; }
  .address {
    position: absolute;
    right: 34px; top: 156px;
    display: flex;
    gap: 8px;
    font-size: 15px;
    line-height: 22px;
    text-align: right;
  }
  .address .icon { margin-top: 4px; }
</style>
</head>
<body>

<section class="card card--back" aria-label="Business card back">
  <div class="wordmark"><span class="wordmark__dot"></span>Keystone Trench Co</div>
  <p class="back-url">www.keystonetrenchco.example</p>
</section>

<section class="card card--front" aria-label="Business card front">
  <span class="front-tab"></span>
  <div class="wordmark"><span class="wordmark__dot"></span>Keystone Trench Co</div>

  <div class="person">
    <p class="person__name">MARCUS HALE</p>
    <p class="person__role">Owner</p>
  </div>

  <div class="divider"></div>

  <ul class="contact-list">
    <li>
      <svg class="icon" viewBox="0 0 16 16" aria-hidden="true"><path fill="var(--accent-red)" d="M3.5 1.5l2.5 3-1.5 1.8c.9 1.9 2.3 3.3 4.2 4.2l1.8-1.5 3 2.5-1.5 2.5C7 14 2 9 1 3z"/></svg>
      555-204-3187
    </li>
    <li>
      <svg class="icon" viewBox="0 0 16 16" aria-hidden="true"><rect x="1.5" y="3.5" width="13" height="9" fill="none" stroke="var(--accent-red)" stroke-width="1.4"/><path d="M1.5 3.5L8 9l6.5-5.5" fill="none" stroke="var(--accent-red)" stroke-width="1.4"/></svg>
      marcus@keystonetrenchco.example
    </li>
    <li>
      <svg class="icon" viewBox="0 0 16 16" aria-hidden="true"><circle cx="8" cy="8" r="6.5" fill="none" stroke="var(--accent-red)" stroke-width="1.4"/><path d="M1.5 8h13M8 1.5c-3 3.5-3 9.5 0 13M8 1.5c3 3.5 3 9.5 0 13" fill="none" stroke="var(--accent-red)" stroke-width="1.2"/></svg>
      www.keystonetrenchco.example
    </li>
  </ul>

  <div class="address">
    <p>Keystone Trench Co Inc.<br>27 Larkfield Road<br>Brookhaven, NL 40213</p>
    <svg class="icon" viewBox="0 0 16 16" aria-hidden="true"><path fill="var(--accent-red)" d="M8 1a5 5 0 0 0-5 5c0 3.8 5 9 5 9s5-5.2 5-9a5 5 0 0 0-5-5zm0 7a2 2 0 1 1 0-4 2 2 0 0 1 0 4z"/></svg>
  </div>
</section>

</body>
</html>
```